Quick Straightforward Billboard Redesign

- Design billboard sized for 10 foot' x 36' foot width live area size and please include bleeds 6" around all sides
- Exact blue color match is imperative in headline, logo, phone number bubble or wherever used. C-83 / M-45 / Y-1 / K-0-
- What I hope to illustrate is that our company offers the best porch screening in the area area, in regards to quality, expertise, durability, storms proof, but we do not build screen porches.
- Current board is attached below from previous designer, and as you can see sizing was off, white space on edges make it appear to be sized incorrectly.
- I also attached my own little mock up idea well well if it helps, favorite image, logo, headline, etc and ideas perhaps on expanding or making this better?

Thanks so much!

Target Market(s)

Drivers and passengers, Southeastern NC, are of immense new construction and high end homes.

Industry/Entity Type

Construction

Colors
0054AA
0677BA
7BADD7
CADEEF
E8F1F8

Requirements
Must have
• Blue color matching
Nice to have
• Design spins or other thoughts on my little mock up

```html
<!DOCTYPE html>
<html lang="en">
<head>
<meta charset="utf-8">
<title>Pelham Porch Co. Billboard</title>
<link rel="stylesheet" href="https://fonts.googleapis.com/css2?family=Anton&display=swap">
<style>
  :root {
    --brand-blue: #0A70B9;
    --brand-green: #00B35A;
    --board-cream: #F1EEE4;
    --stage-grey: #7A8089;
    --white: #FFFFFF;
    --photo-sky: #8FC1EA;
    --photo-ceiling: #E9ECEF;
    --photo-lawn: #9DB86A;
    --photo-floor: #D9D3C6;
    --photo-wicker: #6E655C;
  }
  * { box-sizing: border-box; margin: 0; padding: 0; }
  html, body {
    width: 1145px;
    height: 1200px;
    overflow: hidden;
    background: var(--stage-grey);
    font-family: "Anton", "Impact", sans-serif;
  }
  .billboard {
    position: absolute;
    left: 40px;
    top: 440px;
    width: 1065px;
    height: 320px;
    background: var(--board-cream);
    overflow: hidden;
    box-shadow: 0 12px 28px rgba(0,0,0,0.35);
  }
  .porch-photo {
    position: absolute;
    left: 0;
    top: 0;
    width: 500px;
    height: 100%;
    background:
      linear-gradient(180deg, var(--photo-ceiling) 0%, var(--photo-ceiling) 22%, var(--photo-sky) 30%, var(--photo-sky) 42%, var(--photo-lawn) 50%, var(--photo-wicker) 62%, var(--photo-floor) 82%, var(--photo-floor) 100%);
    -webkit-mask-image: linear-gradient(90deg, #000 0%, #000 72%, transparent 100%);
    mask-image: linear-gradient(90deg, #000 0%, #000 72%, transparent 100%);
  }
  .headline {
    position: absolute;
    left: 385px;
    top: 16px;
    line-height: 1.02;
    font-size: 84px;
    font-weight: 400;
    letter-spacing: 0.5px;
    white-space: nowrap;
  }
  .headline-line { display: block; }
  .headline-line--blue { color: var(--brand-blue); }
  .headline-line--green { color: var(--brand-green); }
  .brand {
    position: absolute;
    left: 385px;
    top: 214px;
    display: flex;
    align-items: center;
    gap: 16px;
  }
  .brand-square {
    width: 76px;
    height: 76px;
    background: var(--brand-blue);
  }
  .brand-name {
    color: var(--brand-blue);
    font-size: 38px;
    line-height: 1.05;
    letter-spacing: 0.5px;
    white-space: nowrap;
  }
  .phone-pill {
    position: absolute;
    left: 675px;
    top: 213px;
    right: 0;
    height: 78px;
    background: var(--brand-blue);
    border-radius: 22px 0 0 22px;
    display: flex;
    align-items: center;
    padding-left: 14px;
    gap: 12px;
    box-shadow: 0 8px 10px -6px rgba(0,0,0,0.35);
  }
  .phone-icon { width: 44px; height: 44px; flex: none; }
  .phone-number {
    color: var(--white);
    font-size: 56px;
    letter-spacing: 0.5px;
    line-height: 1;
    white-space: nowrap;
  }
</style>
</head>
<body>
  <main class="billboard">
    <div class="porch-photo" role="img" aria-label="Photo of a furnished screened porch with wicker chairs overlooking a lawn and lake"></div>

    <h1 class="headline">
      <span class="headline-line headline-line--blue">Screen your Porch.</span>
      <span class="headline-line headline-line--green">Built for the Coast.</span>
    </h1>

    <div class="brand">
      <div class="brand-square"></div>
      <div class="brand-name">PELHAM<br>PORCH CO.</div>
    </div>

    <div class="phone-pill">
      <svg class="phone-icon" viewBox="0 0 46 46" aria-hidden="true">
        <circle cx="23" cy="23" r="22" fill="#FFFFFF"/>
        <circle cx="23" cy="23" r="18" fill="#00B35A"/>
        <path d="M16.5 13.5c1-.8 2.2-.5 2.8.6l2 3.6c.5.9.3 1.9-.5 2.5l-1.4 1.1c1 2.3 2.8 4.2 5 5.3l1.1-1.4c.6-.8 1.7-1 2.5-.5l3.6 2c1.1.6 1.4 1.9.6 2.8l-1.6 1.9c-1 1.1-2.6 1.5-4 .9-5.3-2.2-9.6-6.5-11.8-11.8-.6-1.4-.2-3 .9-4z" fill="#FFFFFF"/>
        <path d="M25 12.5a9 9 0 0 1 8.5 8.5M25 16.5a5 5 0 0 1 4.5 4.5" stroke="#FFFFFF" stroke-width="1.8" fill="none" stroke-linecap="round"/>
      </svg>
      <span class="phone-number">910.555.0142</span>
    </div>
  </main>
</body>
</html>
```